Unique Business Card Design

Unique Business Card design for our orthotic and prosthetic company. Our logo is on our website, color is light blue. Unique shape (artificial leg shaped, vertical, etc..) preferred. Logo, business name, individual name and basic demographics needed.

Industry/Entity Type

Business

Contact Information for Business Card

Logo, Industry, Phone # Logo, "Prosthetic & Orthotic Services" Place to add individual name and contact info

Colors
cee9f5

Requirements
Must have
• The icon must be there, placement of "Prosthetic & Orthotic Services" can be moved
Nice to have
• Like the mix of light blue, and a little darker blue. One design included the icons from my website which was a nice touch

```html
<!DOCTYPE html>
<html lang="en">
<head>
<meta charset="utf-8">
<title>Limbline Inc. – Business Card</title>
<link rel="stylesheet" href="https://fonts.googleapis.com/css2?family=Open+Sans:ital,wght@0,400;0,700;1,400&display=swap">
<style>
  :root {
    --stage: #3a3a3a;
    --blue: #1f63b6;
    --blue-light: #2f7ad0;
    --white: #ffffff;
    --shadow-grey: #b9bcc1;
    --text-font: "Open Sans", Arial, sans-serif;
  }
  * { margin: 0; padding: 0; box-sizing: border-box; }
  html, body { width: 1200px; height: 950px; overflow: hidden; }
  body {
    background: var(--stage);
    font-family: var(--text-font);
    position: relative;
  }
  .card {
    position: absolute;
    left: 320px;
    width: 560px;
    height: 320px;
    border-radius: 18px;
    overflow: hidden;
  }
  /* Front */
  .card-front {
    top: 125px;
    background: linear-gradient(135deg, var(--blue) 0%, var(--blue-light) 100%);
    color: var(--white);
  }
  .front-mark {
    position: absolute;
    left: 52px; top: 92px;
    width: 104px; height: 104px;
    border-radius: 50%;
    background: var(--white);
  }
  .front-name {
    position: absolute;
    left: 180px; top: 104px;
    font-size: 34px;
    font-weight: 700;
    letter-spacing: 0.5px;
    line-height: 1;
  }
  .front-rule {
    position: absolute;
    left: 180px; top: 148px;
    width: 290px; height: 3px;
    background: var(--white);
  }
  .front-tagline {
    position: absolute;
    left: 196px; top: 156px;
    font-size: 19px;
    font-style: italic;
  }
  .front-web {
    position: absolute;
    left: 0; right: 0; bottom: 34px;
    display: flex; align-items: center; justify-content: center; gap: 14px;
    font-size: 14px;
  }
  .front-web::before, .front-web::after {
    content: ""; width: 130px; height: 1px; background: rgba(255,255,255,0.8);
  }
  /* Back */
  .card-back {
    top: 505px;
    background: var(--white);
  }
  .back-shape { position: absolute; inset: 0; width: 560px; height: 320px; }
  .back-brand {
    position: absolute;
    left: 30px; top: 116px;
    display: flex; align-items: center; gap: 12px;
    color: var(--blue);
  }
  .back-mark {
    width: 70px; height: 70px; border-radius: 50%; background: var(--blue);
    flex: none;
  }
  .back-name { font-size: 22px; font-weight: 700; line-height: 1.1; white-space: nowrap; }
  .back-tagline { font-size: 11.5px; font-style: italic; margin-top: 4px; border-top: 2px solid var(--blue); padding-top: 3px; white-space: nowrap; }
  .contact {
    position: absolute;
    right: 24px; top: 62px;
    text-align: right;
    color: var(--white);
  }
  .contact-person { font-size: 21px; font-weight: 700; line-height: 1.1; }
  .contact-title { font-size: 13px; font-weight: 700; margin-bottom: 8px; }
  .contact-list { list-style: none; font-size: 13px; line-height: 23px; }
  .contact-list li { display: flex; justify-content: flex-end; align-items: center; gap: 8px; white-space: nowrap; }
  .contact-list svg { width: 14px; height: 14px; fill: var(--white); flex: none; }
</style>
</head>
<body>

<section class="card card-front" aria-label="Business card front">
  <div class="front-mark"></div>
  <div class="front-name">LIMBLINE INC.</div>
  <div class="front-rule"></div>
  <div class="front-tagline">Prosthetic &amp; Orthotic Services</div>
  <div class="front-web">www.limblineinc.com</div>
</section>

<section class="card card-back" aria-label="Business card back">
  <svg class="back-shape" viewBox="0 0 560 320" aria-hidden="true">
    <defs>
      <linearGradient id="backBlue" x1="0" y1="0" x2="1" y2="1">
        <stop offset="0" stop-color="#1f63b6"/>
        <stop offset="1" stop-color="#2f7ad0"/>
      </linearGradient>
    </defs>
    <path d="M392 0 C 376 175 280 262 96 282 L 0 288 L 0 320 L 560 320 L 560 0 Z" fill="#b9bcc1"/>
    <path d="M410 0 C 394 185 296 272 110 296 L 0 304 L 0 320 L 560 320 L 560 0 Z" fill="url(#backBlue)"/>
  </svg>

  <div class="back-brand">
    <div class="back-mark"></div>
    <div>
      <div class="back-name">LIMBLINE INC.</div>
      <div class="back-tagline">Prosthetic &amp; Orthotic Services</div>
    </div>
  </div>

  <div class="contact">
    <div class="contact-person">Mara Ellison</div>
    <div class="contact-title">CO LPO</div>
    <ul class="contact-list">
      <li>555.210.4400 <svg viewBox="0 0 16 16"><path d="M3 1h3l1 4-2 1a9 9 0 0 0 5 5l1-2 4 1v3c0 1-1 2-2 2A13 13 0 0 1 1 3c0-1 1-2 2-2z"/></svg></li>
      <li>555.210.4419 <svg viewBox="0 0 16 16"><path d="M4 0h8a1 1 0 0 1 1 1v14a1 1 0 0 1-1 1H4a1 1 0 0 1-1-1V1a1 1 0 0 1 1-1zm1 2v10h6V2z"/></svg></li>
      <li>555.388.2716 <svg viewBox="0 0 16 16"><path d="M4 1h7v4H4zM1 6h14v7H1zm2 2v1h4V8zm0 2v1h4v-1z"/></svg></li>
      <li>mellison@limblineinc.com <svg viewBox="0 0 16 16"><path d="M1 3h14v10H1zm1 1v1l6 4 6-4V4z"/></svg></li>
      <li>www.limblineinc.com <svg viewBox="0 0 16 16"><path d="M8 1a7 7 0 1 0 0 14A7 7 0 0 0 8 1zm0 2a5 5 0 1 1 0 10A5 5 0 0 1 8 3z"/></svg></li>
      <li>82 Harbor Ave., Fairview, NY 10990 <svg viewBox="0 0 16 16"><path d="M8 0a5 5 0 0 0-5 5c0 4 5 11 5 11s5-7 5-11a5 5 0 0 0-5-5zm0 3a2 2 0 1 1 0 4 2 2 0 0 1 0-4z"/></svg></li>
    </ul>
  </div>
</section>

</body>
</html>
```